Young, dynamic furniture company needs a new business card design

We require a new business card design for our modern furniture company which supplies furniture and appliances to the property and development market.
Oakridge Interiors has become one of the leading furniture & appliance suppliers to the property market withing London. With over 10 years experience, we have increased our business to supply not only private landlords and managing agents, but also property developers, housing associations and local councils.
We offer not only a complete range of furniture which includes beds, wardrobes, dining sets and sofas, but also a high quality, full delivery and assembly service to help you with all our furnishing needs.

Target Market(s)

Private landlords, estate agents, letting agents, property management companies

Industry/Entity Type

Business

Contact Information for Business Card

Name,
Title,
Address,
Mobile,
Telephone,
Fax, Website, email address

Font styles to use
Sans Serif

Colors
3176b5
0555a3
85abd2
cfdeed

Requirements
Must have
• All the above information for each of our staff, along with our logo

```html
<!DOCTYPE html>
<html lang="en">
<head>
<meta charset="utf-8">
<title>Oakridge Interiors – Business Card</title>
<link href="https://fonts.googleapis.com/css2?family=Barlow+Semi+Condensed:wght@300;400&family=Montserrat:wght@700&family=Questrial&display=swap" rel="stylesheet">
<style>
  :root {
    --navy: #213d73;
    --blue: #1e6fb5;
    --ink: #222222;
    --white: #ffffff;
    --backdrop: #efebe4;
  }
  * { margin: 0; padding: 0; box-sizing: border-box; }
  html, body { width: 1189px; height: 1200px; overflow: hidden; }
  body {
    background: var(--backdrop);
    position: relative;
    font-family: "Questrial", sans-serif;
    color: var(--ink);
  }
  .card {
    position: absolute;
    top: 147px;
    width: 482px;
    height: 843px;
    border-radius: 22px;
    overflow: hidden;
  }
  /* Back of card */
  .card-back { left: 75px; background: var(--navy); }
  .back-lockup {
    position: absolute;
    left: 50%;
    top: 50%;
    transform: translate(-50%, -50%) rotate(-90deg);
    margin-left: 7px;
    color: var(--white);
    font-family: "Barlow Semi Condensed", sans-serif;
    font-weight: 300;
    text-align: center;
    white-space: nowrap;
    line-height: 1;
  }
  .back-name { font-size: 78px; letter-spacing: 1px; }
  .back-tagline { font-size: 39px; letter-spacing: 1px; margin-top: 6px; }

  /* Front of card */
  .card-front { left: 630px; background: var(--white); }
  .brand {
    position: absolute;
    top: 150px;
    left: 0; right: 0;
    text-align: center;
  }
  .brand-name {
    display: inline-flex;
    align-items: center;
    gap: 14px;
    font-family: "Barlow Semi Condensed", sans-serif;
    font-weight: 400;
    font-size: 40px;
    color: var(--navy);
    letter-spacing: 0.5px;
  }
  .brand-mark { width: 34px; height: 34px; background: var(--navy); }
  .brand-tagline {
    margin-top: 14px;
    font-family: "Barlow Semi Condensed", sans-serif;
    font-weight: 400;
    font-size: 21px;
    color: var(--ink);
    letter-spacing: 0.5px;
  }
  .details { position: absolute; left: 58px; top: 408px; }
  .person-name {
    font-family: "Montserrat", sans-serif;
    font-weight: 700;
    font-size: 32px;
    color: var(--navy);
    line-height: 1;
  }
  .person-name .surname { color: var(--blue); }
  .person-title { font-size: 23px; margin-top: 2px; }
  .address { margin-top: 34px; font-size: 23.5px; line-height: 29px; }
  .contacts { margin-top: 22px; list-style: none; font-size: 23.5px; line-height: 32px; }
  .contacts li { display: flex; }
  .contacts .label { color: var(--navy); width: 32px; padding-left: 4px; }
  .card-rule {
    position: absolute;
    left: 0; right: 0;
    top: 772px;
    height: 4px;
    background: var(--blue);
  }
  .card-footer {
    position: absolute;
    left: 0; right: 0;
    top: 781px;
    bottom: 0;
    background: var(--navy);
    color: var(--white);
    font-size: 23px;
    text-align: center;
    line-height: 58px;
  }
</style>
</head>
<body>
  <section class="card card-back">
    <div class="back-lockup">
      <div class="back-name">OAKRIDGE INTERIORS</div>
      <div class="back-tagline">TRADE FURNITURE SOLUTIONS</div>
    </div>
  </section>

  <section class="card card-front">
    <div class="brand">
      <div class="brand-name"><span class="brand-mark"></span>OAKRIDGE INTERIORS</div>
      <div class="brand-tagline">TRADE FURNITURE SOLUTIONS</div>
    </div>

    <div class="details">
      <div class="person-name">MARCUS <span class="surname">HALE</span></div>
      <div class="person-title">Managing Director</div>
      <div class="address">
        Trade Showroom &amp; Office<br>
        7B Elmfield Trade Park<br>
        Northbrook London, N14 3QX
      </div>
      <ul class="contacts">
        <li><span class="label">T</span>: 020 7946 0321</li>
        <li><span class="label">F</span>: 020 7946 0388</li>
        <li><span class="label">M</span>: 07700 90 41 27</li>
        <li><span class="label">E</span>: marcus@ori.co.uk</li>
      </ul>
    </div>

    <div class="card-rule"></div>
    <div class="card-footer">www.ori.co.uk</div>
  </section>
</body>
</html>
```